TA BRAMLEY BUSINESS CARD DESIGN PROJECT

We need to utilize our logo that was expertly created on PixelHarbor and now need to match this with a business card design.

```html
<!DOCTYPE html>
<html lang="en">
<head>
<meta charset="utf-8">
<title>TA BRAMLEY Business Card</title>
<link rel="stylesheet" href="https://fonts.googleapis.com/css2?family=Open+Sans:wght@400;600;700&display=swap">
<style>
  :root {
    --stage: #222222;
    --card-dark: #1b1b1c;
    --brand-blue: #1a5bb5;
    --pattern-blue: #1656ab;
    --pattern-deep: #0f3f82;
    --white: #ffffff;
    --rule: #8a8a8a;
  }
  * { margin: 0; padding: 0; box-sizing: border-box; }
  html, body {
    width: 1200px; height: 780px; overflow: hidden;
    background: var(--stage);
    font-family: "Open Sans", Arial, sans-serif;
  }
  .canvas {
    position: relative; width: 1200px; height: 780px;
    display: flex; align-items: center; justify-content: center; gap: 50px;
  }
  .card {
    position: relative; width: 520px; height: 300px; overflow: hidden;
    box-shadow: 0 18px 40px rgba(0,0,0,.55);
  }
  /* Front */
  .card-front { background: var(--card-dark); }
  .front-logo {
    position: absolute; left: 40px; top: 100px; width: 200px;
    display: flex; align-items: center; gap: 10px;
    color: var(--brand-blue); font-weight: 700; font-size: 26px; letter-spacing: 2px;
  }
  .front-logo .mark { width: 18px; height: 18px; background: var(--brand-blue); flex: none; }
  .divider { position: absolute; left: 0; top: 0; width: 520px; height: 300px; }
  .identity { position: absolute; left: 292px; top: 62px; }
  .person-name { color: var(--brand-blue); font-weight: 700; font-size: 26px; line-height: 1.1; }
  .person-title { color: var(--white); font-size: 14px; margin-top: 4px; }
  .contacts { list-style: none; margin-top: 18px; }
  .contacts li {
    display: flex; align-items: center; gap: 8px;
    color: var(--white); font-size: 14px; line-height: 24px;
  }
  .contacts svg { width: 12px; height: 12px; flex: none; }
  .address-band {
    position: absolute; left: 0; bottom: 0; width: 100%; height: 34px;
    background: var(--brand-blue);
    display: flex; align-items: center; padding-left: 40px;
    color: var(--white); font-size: 13.5px;
  }
  .band-corner {
    position: absolute; right: 0; bottom: 0; width: 46px; height: 34px; background: var(--white);
  }
  /* Back */
  .card-back { background: var(--pattern-blue); }
  .back-pattern {
    position: absolute; inset: 0;
    background: linear-gradient(120deg, var(--pattern-blue) 0%, var(--pattern-deep) 55%, var(--pattern-blue) 100%);
  }
  .back-logo {
    position: absolute; right: 60px; bottom: 46px;
    display: flex; align-items: center; gap: 8px;
    color: var(--white); font-weight: 700; font-size: 18px; letter-spacing: 1.5px;
  }
  .back-logo .mark { width: 12px; height: 12px; background: var(--white); }
</style>
</head>
<body>
<main class="canvas">
  <section class="card card-front" aria-label="Business card front">
    <div class="front-logo"><span class="mark"></span><span>TA BRAMLEY</span></div>
    <svg class="divider" viewBox="0 0 520 300" aria-hidden="true">
      <line x1="262" y1="40" x2="248" y2="250" stroke="var(--rule)" stroke-width="1"/>
    </svg>
    <div class="identity">
      <h1 class="person-name">Marta Kovel</h1>
      <p class="person-title">Managing Director</p>
      <ul class="contacts">
        <li>
          <svg viewBox="0 0 12 12"><path d="M2.5 1l2 2.3-1 1.2a6 6 0 0 0 4 4l1.2-1L11 9.5 9.6 11C5 11 1 7 1 2.4z" fill="var(--brand-blue)"/></svg>
          (555) 201-4836
        </li>
        <li>
          <svg viewBox="0 0 12 12"><rect x="1" y="2.5" width="10" height="7" fill="var(--brand-blue)"/><path d="M1 2.5l5 4 5-4" stroke="var(--white)" stroke-width="0.9" fill="none"/></svg>
          info@tabramley.com
        </li>
        <li>
          <svg viewBox="0 0 12 12"><circle cx="6" cy="6" r="5" fill="var(--brand-blue)"/><path d="M1 6h10M6 1c-2.5 3-2.5 7 0 10M6 1c2.5 3 2.5 7 0 10" stroke="var(--card-dark)" stroke-width="0.7" fill="none"/></svg>
          www.tabramley.com
        </li>
      </ul>
    </div>
    <div class="address-band">418 Linden Ave. Suite 120 Harbor City, TX 75010</div>
    <div class="band-corner"></div>
  </section>

  <section class="card card-back" aria-label="Business card back">
    <div class="back-pattern" role="img" aria-label="Repeating brand pattern in light and deep blue tones"></div>
    <div class="back-logo"><span class="mark"></span><span>TA BRAMLEY</span></div>
  </section>
</main>
</body>
</html>
```